Business Recognition Design

We need a design for a recognition to be given to business leaders in our community.
The recognition shall be made on a brass plaque on wood panel background (picture attached, please use it as a background), and all drawing must be in vectors and only one color (black).
It should also have a logo on the top and signature on the right bottom.
The text is enclosed in DOC file.
Updates

Reason: just to be able to find the best solution

Reason: None of the suggestion is good enough. Logo in general is too big in comparison with the rest of the plate.

Industry/Entity Type

Business

Requirements
Must have
• - standard Windows font (or possibility to install the same font on Windows), as the name on the recognition shall be printed in the same font
Nice to have
• - some graphic element (in curves) representing achievements in business
- should look great :)

```html
<!DOCTYPE html>
<html lang="en">
<head>
<meta charset="UTF-8">
<title>Business Recognition Plaque</title>
<link rel="stylesheet" href="https://fonts.googleapis.com/css2?family=Cinzel:wght@700&family=Alegreya:ital,wght@1,500&family=Open+Sans:wght@400&display=swap">
<style>
  :root {
    --wall: #c8986d;
    --wall-deep: #b9875c;
    --wood-dark: #4e2a16;
    --wood: #74452a;
    --wood-light: #8d5a38;
    --brass-deep: #c99a22;
    --brass: #e2bb3c;
    --brass-light: #f4dc7c;
    --ink: #1e1a14;
    --screw: #a57a1f;
    --screw-light: #f0d27a;
  }
  html, body {
    margin: 0;
    padding: 0;
    width: 1200px;
    height: 973px;
    overflow: hidden;
  }
  body {
    background: radial-gradient(ellipse at center, var(--wall) 0%, var(--wall-deep) 100%);
  }
  .canvas {
    position: relative;
    width: 1200px;
    height: 973px;
  }
  .wall-pattern {
    position: absolute;
    inset: 0;
    background: radial-gradient(ellipse at center, var(--wall) 0%, var(--wall-deep) 100%);
  }
  .wood-panel {
    position: absolute;
    left: 19px;
    top: 38px;
    width: 1162px;
    height: 897px;
    background: linear-gradient(135deg, var(--wood-light) 0%, var(--wood) 45%, var(--wood-dark) 100%);
    box-shadow: 4px 6px 10px rgba(60, 30, 10, 0.45), inset 0 0 0 10px rgba(0, 0, 0, 0.12);
    border-radius: 3px;
  }
  .brass-plate {
    position: absolute;
    left: 65px;
    top: 86px;
    width: 1068px;
    height: 803px;
    background: linear-gradient(100deg, var(--brass-deep) 0%, var(--brass) 35%, var(--brass-light) 62%, var(--brass) 82%, var(--brass-deep) 100%);
    box-shadow: inset 0 0 0 2px rgba(255, 240, 180, 0.6), 2px 3px 6px rgba(0, 0, 0, 0.4);
  }
  .screw {
    position: absolute;
    width: 30px;
    height: 30px;
    border-radius: 50%;
    background: radial-gradient(circle at 35% 35%, var(--screw-light) 0%, var(--brass) 45%, var(--screw) 100%);
    box-shadow: 1px 2px 3px rgba(0, 0, 0, 0.45);
  }
  .screw--tl { left: 90px; top: 104px; }
  .screw--tr { left: 1090px; top: 104px; }
  .screw--bl { left: 90px; top: 834px; }
  .screw--br { left: 1090px; top: 834px; }
  .trophy-art {
    position: absolute;
    left: 108px;
    top: 146px;
    width: 229px;
    height: 205px;
  }
  .medal-art {
    position: absolute;
    left: 884px;
    top: 148px;
    width: 167px;
    height: 225px;
  }
  .plate-text {
    position: absolute;
    left: 65px;
    width: 1068px;
    margin: 0;
    text-align: center;
    color: var(--ink);
  }
  .logo-name {
    top: 166px;
    font-family: "Open Sans", sans-serif;
    font-weight: 400;
    font-size: 48px;
    line-height: 60px;
  }
  .title {
    top: 310px;
    font-family: "Cinzel", serif;
    font-weight: 700;
    font-size: 58px;
    line-height: 72px;
    letter-spacing: 1px;
  }
  .script {
    font-family: "Alegreya", serif;
    font-style: italic;
    font-weight: 500;
  }
  .award-name { top: 406px; font-size: 35px; line-height: 44px; }
  .award-to { top: 455px; font-size: 33px; line-height: 44px; }
  .recipient { top: 512px; font-size: 26px; line-height: 36px; }
  .citation {
    top: 606px;
    font-size: 24px;
    line-height: 48px;
  }
  .footer-date {
    position: absolute;
    left: 178px;
    top: 803px;
    margin: 0;
    font-family: "Open Sans", sans-serif;
    font-size: 21px;
    color: var(--ink);
  }
  .signature {
    position: absolute;
    left: 897px;
    top: 797px;
    width: 135px;
    text-align: center;
    border-top: 1.5px solid var(--ink);
    font-family: "Open Sans", sans-serif;
    font-size: 21px;
    line-height: 34px;
    color: var(--ink);
  }
</style>
</head>
<body>
<div class="canvas">
  <div class="wall-pattern" role="img" aria-label="Ornamental tan damask wallpaper behind the plaque"></div>
  <div class="wood-panel"></div>
  <div class="brass-plate"></div>

  <span class="screw screw--tl"></span>
  <span class="screw screw--tr"></span>
  <span class="screw screw--bl"></span>
  <span class="screw screw--br"></span>

  <svg class="trophy-art" viewBox="0 0 229 205" role="img" aria-label="Gold trophy cup framed by laurel branches">
    <defs>
      <radialGradient id="trophyTone" cx="50%" cy="45%" r="55%">
        <stop offset="0%" stop-color="#f6d96a"/>
        <stop offset="100%" stop-color="#c8931c" stop-opacity="0.6"/>
      </radialGradient>
    </defs>
    <ellipse cx="114" cy="102" rx="112" ry="100" fill="url(#trophyTone)"/>
  </svg>

  <svg class="medal-art" viewBox="0 0 167 225" role="img" aria-label="Gold medal hanging from a red, white and blue ribbon">
    <defs>
      <linearGradient id="medalTone" x1="0" y1="0" x2="0" y2="1">
        <stop offset="0%" stop-color="#b5303a" stop-opacity="0.55"/>
        <stop offset="45%" stop-color="#e3b43a"/>
        <stop offset="100%" stop-color="#c8931c"/>
      </linearGradient>
    </defs>
    <rect x="0" y="0" width="167" height="225" rx="60" fill="url(#medalTone)"/>
  </svg>

  <p class="plate-text logo-name">(Our Logo)</p>
  <h1 class="plate-text title">RECOGNITION</h1>
  <p class="plate-text script award-name">The Best Entrepreneur in 2013</p>
  <p class="plate-text script award-to">to</p>
  <p class="plate-text script recipient">Mr. Daniel R. Whitford, MBA</p>
  <p class="plate-text script citation">
    Under the leadership of Mr. Daniel R. Whitford, MBA<br>
    the company DR-WHITFORD Ltd has been selected<br>
    by a City Council as the best company of The City.
  </p>

  <p class="footer-date">4th July, 2013</p>
  <div class="signature">City Mayor</div>
</div>
</body>
</html>
```